Borvik Media - Amazing Homepage

We would like to build an amazing homepage for our site. We will need it built in HTM5, so it works across devices and would like it to parallax scroll , so it looks amazing.
We are a digital media agency, that has recently launched. Our old site is self build through one of the standard web build sites. We will be hosting our new site independently.
This is our old site - www.borvik-media.example
The new site only really needs one scrolling page to explain what we do and have our contact details at the bottom.
We have a place to host it, once designed. So we can share with the final design for you to upload.
Attached are:
Brief
Logos and artwork
Our PowerPoint template to give you an idea of colours

```html
<!DOCTYPE html>
<html lang="en">
<head>
<meta charset="utf-8">
<title>Borvik Media – Homepage</title>
<link rel="stylesheet" href="https://fonts.googleapis.com/css2?family=Open+Sans:wght@300;400;600;700&display=swap">
<style>
:root{
  --maroon:#7b1a3a;
  --maroon-dark:#5e1029;
  --ink:#333333;
  --muted:#666666;
  --paper:#ffffff;
  --soft:#f1f1f1;
  --night:#1d1f22;
  --white:#ffffff;
}
*{box-sizing:border-box;margin:0;padding:0}
html,body{width:1200px;height:3696px;overflow:hidden}
body{font-family:"Open Sans",Arial,sans-serif;color:var(--ink);background:var(--paper);position:relative}
.section{position:absolute;left:0;width:1200px;overflow:hidden}
.chevron{position:absolute;left:576px;bottom:0;width:48px;height:22px;background:var(--maroon);border-radius:4px 4px 0 0;z-index:3}
.chevron svg{display:block;margin:5px auto 0}

/* header */
.site-header{top:0;height:88px;background:var(--paper);border-bottom:1px solid #e6e6e6}
.brand{position:absolute;left:120px;top:22px;display:flex;align-items:center;gap:12px}
.brand-dot{width:40px;height:40px;border-radius:50%;border:2px solid var(--maroon)}
.brand-name{font-size:18px;font-weight:600;color:var(--ink);letter-spacing:1px;text-transform:uppercase}
.main-nav{position:absolute;right:130px;top:34px;display:flex;gap:34px;font-size:11px;font-weight:600;letter-spacing:.5px}
.main-nav a{color:var(--muted);text-decoration:none}
.main-nav a.active{color:var(--maroon);border-bottom:2px solid var(--maroon);padding-bottom:4px}

/* photo sections */
.photo{position:absolute;inset:0}
.hero{top:88px;height:492px;border-bottom:4px solid var(--maroon)}
.hero .photo{background:radial-gradient(ellipse at 30% 40%,#6b6e73 0%,#3a3c40 45%,#1a1b1d 100%)}
.statement{position:absolute;left:0;width:1200px;text-align:center;color:var(--white);z-index:2}
.statement h1,.statement h2{font-size:28px;font-weight:700;text-transform:uppercase;letter-spacing:.3px}
.statement p{font-size:14px;line-height:22px;width:720px;margin:12px auto 0;opacity:.9}
.btn-outline{display:inline-block;margin-top:38px;padding:14px 30px;border:1px solid var(--white);color:var(--white);font-size:12px;font-weight:600;letter-spacing:1px}

/* welcome */
.welcome{top:580px;height:452px;background:var(--paper)}
.heading-maroon{color:var(--maroon);font-size:26px;font-weight:700;text-transform:uppercase;text-align:center}
.welcome h2{position:absolute;top:34px;width:1200px}
.welcome .intro{position:absolute;top:80px;left:220px;width:760px;text-align:center;font-size:12px;line-height:20px;color:var(--muted)}
.welcome .kicker{position:absolute;top:180px;width:1200px;text-align:center;font-size:11px;font-weight:600;color:var(--muted);letter-spacing:.5px}
.cards{position:absolute;top:216px;left:180px;display:flex;gap:40px}
.card{width:180px;height:196px;background:var(--soft);box-shadow:0 2px 6px rgba(0,0,0,.18);text-align:center;padding:30px 16px 0}
.card-icon{width:56px;height:56px;margin:0 auto 22px;display:flex;align-items:center;justify-content:center}
.card p{font-size:11px;line-height:17px;color:var(--muted)}

/* maroon bands */
.band{background:var(--maroon);color:var(--white);text-align:center;font-weight:300;font-size:30px}
.band-one{top:1032px;height:128px;line-height:118px}
.band-two{top:1912px;height:128px;line-height:118px}
.band-contact{top:2848px;height:112px;line-height:104px;font-size:32px}

/* every client */
.every-client{top:1160px;height:440px;border-bottom:4px solid var(--maroon)}
.every-client .photo{background:radial-gradient(circle at 50% 55%,#8a7a3a 0%,#4a4a3e 35%,#2a2b2c 75%)}

/* coup */
.coup{top:1600px;height:312px;background:var(--paper)}
.coup .lead{position:absolute;left:180px;top:30px;width:840px;color:var(--maroon);font-size:15px;font-weight:700;line-height:22px;text-align:center}
.coup .media{position:absolute;left:180px;top:112px;width:380px;height:170px;background:linear-gradient(135deg,#d9dde2,#9aa3ac)}
.coup .body{position:absolute;left:600px;top:108px;width:420px;font-size:11px;line-height:18px;color:var(--muted)}
.coup .body p+p{margin-top:10px}

/* growth */
.growth{top:2040px;height:420px;border-top:4px solid var(--maroon)}
.growth .photo{background:linear-gradient(180deg,#3b3e43 0%,#26282b 100%)}
.growth h2{position:absolute;top:36px;width:1200px;text-align:center;color:var(--white);font-size:26px;font-weight:700;line-height:34px;text-transform:uppercase}
.growth .sub{position:absolute;top:112px;width:1200px;text-align:center;color:#dddddd;font-size:13px}
.services{position:absolute;top:162px;left:180px;display:flex;gap:24px}
.service{width:192px}
.service-img{height:150px}
.service-label{background:var(--paper);color:var(--ink);font-size:12px;font-weight:600;padding:8px 12px}
.arrow{position:absolute;top:214px;width:34px;height:34px;border-radius:50%;border:2px solid #cfcfcf;display:flex;align-items:center;justify-content:center}
.growth .board{position:absolute;top:370px;width:1200px;text-align:center;color:var(--white);font-size:14px;font-weight:700;text-transform:uppercase}

/* results */
.results{top:2460px;height:388px;background:var(--paper)}
.results h2{position:absolute;top:32px;left:180px;width:840px;font-size:22px;line-height:32px}
.results .sub{position:absolute;top:112px;width:1200px;text-align:center;font-size:11px;font-weight:700;color:var(--ink);text-transform:uppercase}
.results .mark{position:absolute;top:160px;width:1200px;display:flex;flex-direction:column;align-items:center;gap:10px}
.results .mark .ring{width:70px;height:70px;border-radius:50%;border:2px solid var(--maroon)}
.results .mark span{font-size:20px;font-weight:600;letter-spacing:2px;text-transform:uppercase;color:var(--ink)}
.clients{position:absolute;top:302px;left:150px;width:900px;display:flex;justify-content:space-between;align-items:center}
.client{display:flex;align-items:center;gap:8px;font-size:20px;font-weight:700;color:#555555}
.client i{width:16px;height:16px;background:#555555;display:block}

/* contact */
.contact{top:2960px;height:580px}
.contact .photo{background:radial-gradient(ellipse at 70% 50%,#3a4652 0%,#1f252b 55%,#121416 100%)}
.contact h3{font-size:14px;font-weight:700;color:var(--white);text-transform:uppercase}
.contact-info{position:absolute;left:180px;top:60px;width:220px;color:#dddddd;font-size:12px;line-height:19px}
.contact-info dl{margin-top:18px}
.contact-info dd{margin-bottom:12px}
.contact-form{position:absolute;left:460px;top:60px;width:560px}
.field-row{display:flex;gap:20px;margin-top:18px}
.field{flex:1;height:34px;background:var(--paper);border:1px solid #cccccc;font-size:11px;color:#999999;padding:9px 12px}
.field.tall{height:120px}
.submit{margin-top:18px;margin-left:auto;width:150px;height:40px;border:1px solid var(--white);color:var(--white);font-size:12px;font-weight:600;letter-spacing:1px;display:flex;align-items:center;justify-content:center}

/* footer */
.site-footer{top:3540px;height:156px;background:var(--paper);text-align:center}
.socials{position:absolute;top:40px;width:1200px;display:flex;justify-content:center;gap:14px}
.socials span{width:18px;height:18px;border-radius:50%;background:var(--maroon)}
.footer-links{position:absolute;top:84px;width:1200px;display:flex;justify-content:center;gap:26px;font-size:10px;color:var(--muted);text-transform:uppercase}
.copyright{position:absolute;top:114px;width:1200px;font-size:9px;color:#999999}
</style>
</head>
<body>

<header class="section site-header">
  <div class="brand"><span class="brand-dot"></span><span class="brand-name">Borvik Media</span></div>
  <nav class="main-nav">
    <a class="active">HOME</a><a>ABOUT US</a><a>WHAT WE CAN OFFER</a><a>CONTACT</a>
    <svg width="12" height="12" viewBox="0 0 12 12"><circle cx="5" cy="5" r="3.6" fill="none" stroke="#666" stroke-width="1.4"/><line x1="7.6" y1="7.6" x2="11" y2="11" stroke="#666" stroke-width="1.4"/></svg>
  </nav>
</header>

<section class="section hero">
  <div class="photo" role="img" aria-label="Close-up photo of a person wearing glasses, darkened"></div>
  <div class="statement" style="top:200px">
    <h1>Got the feeling your digital marketing just isn't quite 'there'?</h1>
    <p>Lorem ipsum dolor sit amet, consectetuer adipiscing elit, sed diam nonummy nibh euismod tincidunt ut laoreet dolore magna aliquam erat volutpat.</p>
    <span class="btn-outline">LEARN MORE</span>
  </div>
  <div class="chevron"><svg width="14" height="9" viewBox="0 0 14 9"><polyline points="2,2 7,7 12,2" fill="none" stroke="#fff" stroke-width="2"/></svg></div>
</section>

<section class="section welcome">
  <h2 class="heading-maroon">Welcome to Borvik-Media</h2>
  <p class="intro">Borvik is a media agency that is obsessed with delivering excellent media planning, buying and analysis. We believe that the art of planning is crucial and that we should be supported by science. We have the skills to manage, measure and grow results, and we bring the experience to translate this into understanding markets, customers and business. This enables us to prioritise opportunities, identify threats and get our clients' campaigns in front of the right people at the right time.</p>
  <p class="kicker">WE KEEP FIGHTING TO GIVE YOU CLARITY BY:</p>
  <div class="cards">
    <div class="card">
      <div class="card-icon"><svg width="48" height="48" viewBox="0 0 48 48"><circle cx="24" cy="24" r="18" fill="none" stroke="#7b1a3a" stroke-width="4"/><circle cx="24" cy="24" r="10" fill="none" stroke="#7b1a3a" stroke-width="4"/><circle cx="24" cy="24" r="3" fill="#7b1a3a"/></svg></div>
      <p>Creating a regular view of your digital eco system</p>
    </div>
    <div class="card">
      <div class="card-icon"><svg width="48" height="48" viewBox="0 0 48 48"><circle cx="24" cy="24" r="19" fill="#7b1a3a"/><ellipse cx="24" cy="24" rx="8" ry="19" fill="none" stroke="#fff" stroke-width="2"/><line x1="5" y1="24" x2="43" y2="24" stroke="#fff" stroke-width="2"/></svg></div>
      <p>Reviewing how and why your money is being spent where it is</p>
    </div>
    <div class="card">
      <div class="card-icon"><svg width="52" height="48" viewBox="0 0 52 48"><circle cx="26" cy="16" r="8" fill="#7b1a3a"/><path d="M12 40c0-9 6-14 14-14s14 5 14 14z" fill="#7b1a3a"/><circle cx="10" cy="20" r="5" fill="#7b1a3a"/><circle cx="42" cy="20" r="5" fill="#7b1a3a"/><path d="M1 38c0-6 4-10 9-10s6 2 6 2l-3 8z M51 38c0-6-4-10-9-10s-6 2-6 2l3 8z" fill="#7b1a3a"/></svg></div>
      <p>Profiling your customers. Who doesn't have 1000's of different customers with different motivations, lives and value to the brand?</p>
    </div>
    <div class="card">
      <div class="card-icon"><svg width="48" height="48" viewBox="0 0 48 48"><rect x="6" y="22" width="8" height="20" fill="#7b1a3a"/><path d="M17 22l8-14c3 0 5 2 4 6l-2 6h12c3 0 4 3 3 5l-4 14c-1 2-2 3-4 3H17z" fill="#7b1a3a"/></svg></div>
      <p>Finding the best digital channels to communicate with them because every thing is changing every day... exciting isn't it.</p>
    </div>
  </div>
</section>

<section class="section band band-one">Never stop, never settle, always improve. Be amazing.
  <div class="chevron" style="background:var(--maroon-dark)"><svg width="14" height="9" viewBox="0 0 14 9"><polyline points="2,2 7,7 12,2" fill="none" stroke="#fff" stroke-width="2"/></svg></div>
</section>

<section class="section every-client">
  <div class="photo" role="img" aria-label="Photo of colourful glass spheres on a dark table"></div>
  <div class="statement" style="top:116px">
    <h2>Every client deserves amazing work, regardless of the brand, it's all real money</h2>
    <p>Lorem ipsum dolor sit amet, consectetuer adipiscing elit, sed diam nonummy nibh euismod tincidunt ut laoreet dolore magna aliquam erat volutpat.</p>
    <span class="btn-outline">LEARN MORE</span>
  </div>
  <div class="chevron"><svg width="14" height="9" viewBox="0 0 14 9"><polyline points="2,2 7,7 12,2" fill="none" stroke="#fff" stroke-width="2"/></svg></div>
</section>

<section class="section coup">
  <p class="lead">It's time to start a coup...there are too many large agency networks, too few agencies being transparent, too many putting quality of work second to income</p>
  <div class="media" role="img" aria-label="Photo of hands typing on a laptop keyboard"></div>
  <div class="body">
    <p>Ut wisi enim ad minim veniam, quis nostrud exerci tation ullamcorper suscipit lobortis nisl ut aliquip ex ea commodo consequat.</p>
    <p>Duis autem vel eum iriure dolor in hendrerit in vulputate velit esse molestie consequat, vel illum dolore eu feugiat nulla facilisis at vero eros et accumsan et iusto odio dignissim qui blandit praesent luptatum zzril delenit augue duis dolore te feugait nulla facilisi.</p>
    <p>Nam liber tempor cum soluta nobis eleifend option congue nihil imperdiet doming id quod mazim placerat facer possim assum typi non habent claritatem insitam.</p>
  </div>
</section>

<section class="section band band-two">Well, a very quiet coup.
  <div class="chevron" style="background:var(--maroon-dark)"><svg width="14" height="9" viewBox="0 0 14 9"><polyline points="2,2 7,7 12,2" fill="none" stroke="#fff" stroke-width="2"/></svg></div>
</section>

<section class="section growth">
  <div class="photo" role="img" aria-label="Dark blurred office background"></div>
  <h2>We've yet to come across a client that wants to shrink...<br>making us specialists in delivering growth!</h2>
  <p class="sub">We've been optimising our digital knowledge for over 20 years and we genuinely know what we're talking about</p>
  <div class="arrow" style="left:118px"><svg width="12" height="12" viewBox="0 0 12 12"><polyline points="8,1 3,6 8,11" fill="none" stroke="#cfcfcf" stroke-width="2"/></svg></div>
  <div class="arrow" style="left:1048px"><svg width="12" height="12" viewBox="0 0 12 12"><polyline points="4,1 9,6 4,11" fill="none" stroke="#cfcfcf" stroke-width="2"/></svg></div>
  <div class="services">
    <div class="service"><div class="service-img" role="img" aria-label="Photo of a keyboard and mouse" style="background:linear-gradient(135deg,#e8e8e8,#9a9a9a)"></div><div class="service-label">PPC</div></div>
    <div class="service"><div class="service-img" role="img" aria-label="Photo of a search engine page on screen" style="background:linear-gradient(135deg,#f2f2f2,#c9ced6)"></div><div class="service-label">SEO</div></div>
    <div class="service"><div class="service-img" role="img" aria-label="Photo of a display billboard against the sky" style="background:linear-gradient(180deg,#4a7ec0,#9a2f3a)"></div><div class="service-label">DISPLAY</div></div>
    <div class="service"><div class="service-img" role="img" aria-label="Colourful illustration of raised hands" style="background:linear-gradient(135deg,#e0b340,#3f9e6a,#3a6fc4)"></div><div class="service-label">PAID SOCIAL</div></div>
  </div>
  <p class="board">Operating at board level in top 10 digital agencies</p>
</section>

<section class="section results">
  <h2 class="heading-maroon">Happily, we smash it for all our clients, with an average of 35% improvement in performance</h2>
  <p class="sub">Within the first quarter of working with us</p>
  <div class="mark"><span class="ring"></span><span>Borvik Media</span></div>
  <div class="clients">
    <span class="client"><i></i>Hartwell</span>
    <span class="client">Calmora</span>
    <span class="client">Veyla</span>
    <span class="client"><i></i>Tellbridge Group</span>
    <span class="client">Orrin</span>
  </div>
</section>

<section class="section band band-contact">Contact Us</section>

<section class="section contact">
  <div class="photo" role="img" aria-label="Dark photo of a globe with city lights"></div>
  <div class="contact-info">
    <h3>Get in touch with us</h3>
    <dl>
      <dt>by email:</dt><dd>contact@borvik-media.example</dd>
      <dt>by call:</dt><dd>123 456 789</dd>
      <dt>by location:</dt><dd>20 Harlow Place,<br>London, W1A 0ZZ</dd>
    </dl>
  </div>
  <div class="contact-form">
    <h3>Send us a message</h3>
    <div class="field-row"><div class="field">NAME</div><div class="field">PHONE</div></div>
    <div class="field-row"><div class="field">EMAIL ADDRESS</div></div>
    <div class="field-row"><div class="field tall">MESSAGE</div></div>
    <div class="submit">SUBMIT</div>
  </div>
  <div class="chevron"><svg width="14" height="9" viewBox="0 0 14 9"><polyline points="2,2 7,7 12,2" fill="none" stroke="#fff" stroke-width="2"/></svg></div>
</section>

<footer class="section site-footer">
  <div class="socials" aria-label="Social links"><span></span><span></span><span></span><span></span><span></span><span></span></div>
  <div class="footer-links"><span>Privacy Policy</span><span>Sitemap</span><span>Terms</span><span>Contact Us</span></div>
  <p class="copyright">© Copyright Borvik Media. All rights reserved.</p>
</footer>

</body>
</html>
```